Business card design Needed for new logo / Construction business, home extensions and new builds

We need a business card design using our new logo files which i will attach to this project :)

We are a small construction business specialising in home extensions, new builds and property development. We are very ambitious and would appreciate professional and elegant designs for our new business card.

Very serious about using the services on MakerQuarry and recently acquired our new logo from here :)

Please get involved, i will feedback when i can as i am very busy but can respond daily, thanks

Target Market(s)

People that want to build onto their houses, new building developments or adding too their existing property

Industry/Entity Type

Construction

Contact Information for Business Card

Renwick Tolliver Construction, Lionel Ashby (Managing Director), Tel 07822254961, email - info@renwick-tolliver, www.renwick-tolliver.co.uk

Colors

Designer to choose colors to be used in the design.

Requirements
Must have
• I like a deep grey on the back please. A lot of you have provided black from and back, try mixing things up a little. The black looks cool 😎 Thanks

```html
<!DOCTYPE html>
<html lang="en">
<head>
<meta charset="utf-8">
<title>Renwick Tolliver Construction – Business Card</title>
<link rel="stylesheet" href="https://fonts.googleapis.com/css2?family=Cinzel:wght@400;600&display=swap">
<style>
  :root {
    --backdrop: #b4b4b2;
    --deep-grey: #333333;
    --pattern-grey: #3a3a3a;
    --white: #ffffff;
    --cream-pattern: #fdfbf4;
    --gold: #c9931c;
    --ink: #1c1c1c;
  }
  * { margin: 0; padding: 0; box-sizing: border-box; }
  html, body {
    width: 1200px; height: 850px; overflow: hidden;
    background: var(--backdrop);
    font-family: "Cinzel", serif;
  }
  .canvas { position: relative; width: 1200px; height: 850px; }

  .card {
    position: absolute; left: 325px; width: 552px; height: 331px;
    border-radius: 31px; overflow: hidden;
    box-shadow: 10px 14px 22px rgba(0,0,0,0.28);
  }
  .card--front { top: 76px; background: var(--deep-grey); }
  .card--back { top: 444px; background: var(--white); }

  .pattern-fill { position: absolute; inset: 0; }
  .card--front .pattern-fill {
    background: radial-gradient(ellipse at center, var(--deep-grey) 30%, var(--pattern-grey) 100%);
  }
  .card--back .pattern-fill {
    background: linear-gradient(90deg, var(--white), var(--cream-pattern));
  }

  .brand {
    position: absolute; left: 0; right: 0; top: 118px;
    display: flex; flex-direction: column; align-items: center; gap: 16px;
  }
  .brand__mark { width: 26px; height: 26px; background: var(--gold); }
  .brand__name {
    color: var(--gold); font-weight: 600; font-size: 23px;
    letter-spacing: 1.5px; text-align: center; line-height: 1.3;
    text-transform: uppercase;
  }

  .card__art { position: absolute; inset: 0; }

  .identity { position: absolute; left: 255px; top: 42px; }
  .identity__name {
    font-size: 27px; font-weight: 600; color: var(--gold);
    letter-spacing: 0.5px; line-height: 1; text-transform: uppercase;
  }
  .identity__role {
    font-size: 16px; color: var(--ink); margin-top: 6px; letter-spacing: 0.5px;
    text-transform: uppercase;
  }

  .contacts { position: absolute; left: 256px; top: 0; list-style: none; }
  .contacts__item {
    position: absolute; left: 0; display: flex; align-items: center; gap: 11px;
    white-space: nowrap; font-size: 14.5px; color: var(--ink); letter-spacing: 0.4px;
    line-height: 21px;
  }
  .contacts__icon { width: 21px; height: 21px; flex: none; }
</style>
</head>
<body>
<main class="canvas">

  <section class="card card--front" aria-label="Card front">
    <div class="pattern-fill" role="img" aria-label="Faint repeating brand pattern on deep grey"></div>
    <div class="brand">
      <span class="brand__mark"></span>
      <p class="brand__name">Renwick Tolliver<br>Construction</p>
    </div>
  </section>

  <section class="card card--back" aria-label="Card back">
    <div class="pattern-fill" role="img" aria-label="Very faint repeating brand pattern on white"></div>
    <svg class="card__art" width="552" height="331" viewBox="0 0 552 331">
      <defs>
        <linearGradient id="goldBand" x1="0" y1="0" x2="1" y2="1">
          <stop offset="0" stop-color="#b57f10"/>
          <stop offset="0.45" stop-color="#f3d27a"/>
          <stop offset="1" stop-color="#f6bc2e"/>
        </linearGradient>
        <linearGradient id="silverBand" x1="0" y1="0" x2="1" y2="1">
          <stop offset="0" stop-color="#e4e5e6"/>
          <stop offset="0.5" stop-color="#8e9296"/>
          <stop offset="1" stop-color="#dadbdc"/>
        </linearGradient>
      </defs>
      <polygon class="edge-silver" points="98,0 108,0 202,165 108,331 98,331" fill="url(#silverBand)"/>
      <polygon class="panel-dark" points="0,0 98,0 194,165 98,331 0,331" fill="var(--deep-grey)"/>
      <polygon class="band-gold" points="91,16 118,16 186,135 160,135" fill="url(#goldBand)"/>
      <polygon class="band-silver" points="120,16 128,16 196,135 188,135" fill="url(#silverBand)"/>
      <polygon class="band-gold" points="154,208 191,208 147,287 110,287" fill="url(#goldBand)"/>
    </svg>

    <div class="identity">
      <p class="identity__name">Lionel Ashby</p>
      <p class="identity__role">Managing Director</p>
    </div>

    <ul class="contacts">
      <li class="contacts__item" style="top:140px">
        <svg class="contacts__icon" viewBox="0 0 20 20"><circle cx="10" cy="10" r="10" fill="var(--gold)"/><path d="M10 4.5a3.3 3.3 0 0 0-3.3 3.3c0 2.5 3.3 6.4 3.3 6.4s3.3-3.9 3.3-6.4A3.3 3.3 0 0 0 10 4.5z" fill="#fff"/><circle cx="10" cy="7.8" r="1.2" fill="var(--gold)"/></svg>
        12 Elmstead Road, Kent
      </li>
      <li class="contacts__item" style="top:176px">
        <svg class="contacts__icon" viewBox="0 0 20 20"><circle cx="10" cy="10" r="10" fill="var(--gold)"/><rect x="5" y="6.5" width="10" height="7" fill="#fff"/><path d="M5 6.5l5 4 5-4" fill="none" stroke="var(--gold)" stroke-width="0.9"/></svg>
        info@renwick-tolliver
      </li>
      <li class="contacts__item" style="top:208px">
        <svg class="contacts__icon" viewBox="0 0 20 20"><circle cx="10" cy="10" r="10" fill="var(--gold)"/><g fill="none" stroke="#fff" stroke-width="0.9"><circle cx="10" cy="10" r="5"/><ellipse cx="10" cy="10" rx="2.2" ry="5"/><path d="M5 10h10M6 7.5h8M6 12.5h8"/></g></svg>
        www.renwick-tolliver.co.uk
      </li>
      <li class="contacts__item" style="top:246px">
        <svg class="contacts__icon" viewBox="0 0 20 20"><circle cx="10" cy="10" r="10" fill="var(--gold)"/><path d="M6.5 5.5l2 .2.8 2.3-1.2 1a6 6 0 0 0 2.9 2.9l1-1.2 2.3.8.2 2c-.6.8-1.5 1-2.4.8A8.5 8.5 0 0 1 5.7 7.9c-.2-.9 0-1.8.8-2.4z" fill="#fff"/></svg>
        07822254961
      </li>
    </ul>
  </section>

</main>
</body>
</html>
```